Small Business Consulting Firm Needs Letterhead

We need a letterhead for our company "Brightpath Plus". Our company does outbound calling and mailing to business owner's companies who have taken high interest loans. These loans tend to put these businesses in a big financial bind short term, and we help them find better financial options. We would like the design to match our colors of our logo. Headers and footers would look nice, but we are open. We would want it to include our address, website, phone, and email info. Our address - 2000 E. Lamar Blvd. Suite 600Website - www.safeguardtoday.comEmail - info@safeguardtoday.comPhone - 855-726-1938
Industry/Entity Type
Financial Planning
Look and feel
Each slider illustrates characteristics of the customer's brand and the style your logo design should communicate.

```html
<!DOCTYPE html>
<html lang="en">
<head>
<meta charset="utf-8">
<title>Brightpath Plus Letterhead</title>
<link rel="stylesheet" href="https://fonts.googleapis.com/css2?family=Montserrat:wght@400;500&display=swap">
<style>
  :root {
    --page-bg: #e6e6e4;
    --paper: #ffffff;
    --ink: #2b2b2b;
    --ink-soft: #3c3c3c;
    --green: #6aaa3a;
    --blue: #0a78c2;
  }
  * { margin: 0; padding: 0; box-sizing: border-box; }
  html, body { width: 1200px; height: 1200px; overflow: hidden; }
  body {
    background: var(--page-bg);
    font-family: "Montserrat", sans-serif;
    color: var(--ink);
  }
  .letterhead {
    position: absolute;
    left: 167px; top: 40px;
    width: 865px; height: 1120px;
    background: var(--paper);
    box-shadow: 0 6px 18px rgba(0,0,0,.18);
    overflow: hidden;
  }
  .header-band {
    position: absolute; top: 0; left: 329px; right: 0; height: 14px;
    background: var(--green);
  }
  .side-band {
    position: absolute; top: 0; right: 0; width: 14px; height: 535px;
    background: var(--green);
  }
  .footer-corner { position: absolute; left: 0; bottom: 0; width: 106px; height: 106px; }
  .brand {
    position: absolute; left: 0; right: 0; top: 150px;
    display: flex; justify-content: center; align-items: center; gap: 12px;
  }
  .brand-mark { width: 20px; height: 20px; background: var(--green); }
  .brand-name {
    font-size: 27px; font-weight: 400; letter-spacing: .04em;
    text-transform: uppercase; color: var(--ink-soft);
  }
  .letter {
    position: absolute; left: 108px; width: 705px;
    font-size: 14.6px; letter-spacing: .08em; line-height: 22.9px;
  }
  .date { top: 272px; }
  .recipient { top: 331px; }
  .salutation { top: 476px; }
  .body-copy { top: 509px; line-height: 25.4px; text-align: justify; }
  .body-copy p + p { margin-top: 4px; }
  .closing { top: 818px; }
  .signatory { top: 871px; }
  .signatory .name { font-size: 16.5px; font-weight: 500; }
  .signatory .title { letter-spacing: .3em; }
  .contact {
    position: absolute; top: 1042px; left: 197px;
    display: grid; grid-template-columns: 248px auto; row-gap: 5px;
    font-size: 14px; letter-spacing: .08em; color: var(--ink-soft);
  }
  .contact-item { display: flex; align-items: center; gap: 8px; }
  .contact-item svg { width: 12px; height: 12px; flex: none; }
</style>
</head>
<body>
  <div class="letterhead">
    <div class="header-band"></div>
    <div class="side-band"></div>
    <svg class="footer-corner" viewBox="0 0 106 106" aria-hidden="true">
      <polygon points="0,0 0,106 106,106" fill="var(--blue)"/>
    </svg>

    <div class="brand">
      <span class="brand-mark"></span>
      <span class="brand-name">Brightpath Plus</span>
    </div>

    <div class="letter date">Date: 20 November 2018</div>

    <div class="letter recipient">
      To<br>Maplebrook Nursery Ltd.<br>48 Alder Row, Suite# B<br>Leeds, UK LS4 7QT
    </div>

    <div class="letter salutation">Dear Mr. Carver,</div>

    <div class="letter body-copy">
      <p>Lorem Ipsum is simply dummy text of the printing and typesetting industry. Lorem Ipsum has been the industry's standard dummy text ever since the 1500s, when an unknown printer took a galley of type and scrambled it to make a type specimen book. It has survived not only five centuries, but also the leap into electronic type-setting, remaining essentially unchanged. It was popularised in the 1960s with the release of Lettrafix sheets containing Lorem Ipsum passages, and more recently with desktop publishing software like Quillset Layout including versions of Lorem Ipsum.</p>
      <p>Lorem Ipsum is simply dummy text of the printing and typesetting industry. Lorem Ipsum has been the industry's.</p>
    </div>

    <div class="letter closing">Thanking you</div>

    <div class="letter signatory">
      <div class="name">Daniel Hale Marsh</div>
      <div class="title">CEO</div>
    </div>

    <div class="contact">
      <div class="contact-item">
        <svg viewBox="0 0 12 12"><path d="M2.5 1 4.5 1 5.3 3.4 4 4.4C4.7 5.9 6 7.2 7.6 8L8.6 6.7 11 7.5 11 9.5C11 10.4 10.3 11 9.5 11 5 10.6 1.4 7 1 2.5 1 1.7 1.6 1 2.5 1Z" fill="var(--blue)"/></svg>
        <span>855-726-1938</span>
      </div>
      <div class="contact-item">
        <svg viewBox="0 0 12 12"><rect x="0.5" y="2" width="11" height="8" rx="1" fill="var(--blue)"/><path d="M1 2.8 6 6.3 11 2.8" stroke="#fff" stroke-width="1" fill="none"/></svg>
        <span>info@brightpathplus.com</span>
      </div>
      <div class="contact-item">
        <svg viewBox="0 0 12 12"><circle cx="6" cy="6" r="5" fill="none" stroke="var(--green)" stroke-width="1.2"/><path d="M1 6H11M6 1C3.5 3.8 3.5 8.2 6 11M6 1C8.5 3.8 8.5 8.2 6 11" stroke="var(--green)" stroke-width="1" fill="none"/></svg>
        <span>www.brightpathplus.com</span>
      </div>
      <div class="contact-item">
        <svg viewBox="0 0 12 12"><path d="M6 11.5C6 11.5 2 7 2 4.3A4 4 0 0 1 10 4.3C10 7 6 11.5 6 11.5Z" fill="var(--green)"/><circle cx="6" cy="4.3" r="1.4" fill="#fff"/></svg>
        <span>4170 W. Corwin Ave. Suite 310</span>
      </div>
    </div>
  </div>
</body>
</html>
```